Application page web design and internal pages

Create a web site where home
Page looks like an application screen for a mobile phone

Use bold icons and colors with images that have round edges

PorlenPurse Apps is name of page

Search bar at the top

Use colors from Vextaro.org for background

Price of ZORBS in top right corner (https://www.quelvix.example/trade/en-US?symbol=ZORBS_USDT&layout=basic&theme=dark)

Pages within each app should be the same color as the icon

Use the following as app icons on the page:
Key
Icon name: first screen; second screen (text)

⁃ Balances: enter pin; display balances (Your account can hold multiple currency denominations. Your balances are: ZORBS 1234567890)
⁃ Transactions: enter pin; display transactions (Your last 5 payments are ZORBS 10 from Vextaro)
⁃ Send Money: enter phone number, enter amount, send button; display message
⁃ Create Account: choose country code, enter phone number, create button; enter pin; display message ( (phone number) will be notified when their account has been created)
⁃ My Wallet Address: enter pin; display public key (IMPORTANT Send only STELLAR blockchain tokens to this deposit address: GDXQ7PLM2ZNVA9TRK4WSEY8HCBUJ6FOGDLIXP3QM5RTVKNAWZEHOBCYS)
⁃ Private Message: enter phone number, enter message, choose image, send button; enter pin; display message ( (phone number) will be notified when their message has been created)
⁃ Buy Cryptocurrency: drop drown menu of cryptocurrency to purchase (Bitcoin/Ethereum/Stellar/ZORBS), Amount in USD field, amount in chosen cryptocurrency displayed, frequency drop down menu (once/daily/weekly/monthly), buy button; enter card information (name, card number, expiration date, cvv, billing address, zip code), confirm buy button, transactions will appear on your billing statement as VEXTARO; enter pin screen; display message (You will be notified when your coin is received)
⁃ NFTs: upload image, title, description, link media, create NFT button; enter pin screen; display message (You will be notified when your NFT is created)
⁃ Earn: display message (Earn cryptocurrency doing what you do everyday, coming soon)
⁃ Files/Vault: display message (Storage for your photos, documents and more, coming soon)
⁃ Wealth: display message (Build wealth by working with a financial professional to get you to the next level), check box (I would like a financial professional to contact me about building wealth), contact me button; display message (A financial professional will contact you to achieve your financial goals)
⁃ Education: display message (Learn more about everything, coming soon)
⁃ News: display message (News from around the world, coming soon)
⁃ FAQs: use FAQs from this link https://vextaro.example/faq
⁃ Contact Us: enter message, send button; display message (Thank you for reaching out. We will reply to your message in the order it was received. Your patience is appreciated. Blessings.)

Requirements
Must have
• Application home page that looks like the Home Screen of a mobile phone
Nice to have
• Colorful icons

```html
<!DOCTYPE html>
<html lang="en">
<head>
<meta charset="utf-8">
<title>PorlenPurse Apps – Screens</title>
<link rel="stylesheet" href="https://fonts.googleapis.com/css2?family=Roboto:wght@400;500;700&family=Poppins:wght@400;500&display=swap">
<style>
  :root{
    --canvas:#cbcbcb;
    --navy:#1c1b4a;
    --ink:#25253a;
    --muted:#666676;
    --line:#b9b9c2;
    --teal:#22b8cc;
    --white:#ffffff;
    --shade:rgba(0,0,0,.62);
  }
  *{box-sizing:border-box;margin:0;padding:0}
  html,body{width:1184px;height:1200px;overflow:hidden;background:var(--canvas)}
  body{position:relative;font-family:"Roboto",sans-serif;color:var(--ink)}
  .defs{position:absolute;width:0;height:0}

  .screen{position:absolute;width:393px;height:762px;background:var(--white);overflow:hidden;transform:scale(.621);transform-origin:0 0}
  .screen.tall{height:769px}
  .s1{left:152px;top:81px}
  .s2{left:470px;top:81px}
  .s3{left:786px;top:79px}
  .s4{left:152px;top:634px}
  .s5{left:469px;top:634px}

  .header-wave{position:absolute;left:0;top:0;width:393px;height:310px}
  .brand{position:absolute;left:0;right:0;top:76px;text-align:center;color:var(--white)}
  .brand-mark{display:block;width:20px;height:20px;margin:0 auto 14px;border:2px solid var(--white);border-radius:3px}
  .brand-name{font-weight:500;font-size:18px;letter-spacing:2.6px}

  .price-bar{position:absolute;left:82px;top:160px;width:229px;height:58px;background:var(--navy);border-radius:3px;color:var(--white);font-size:16px;display:flex;align-items:center;justify-content:space-between;padding:0 26px 0 23px}
  .price-bar .coin svg,.price-bar .value svg{vertical-align:middle;margin-left:6px}

  .search{position:absolute;left:40px;top:245px;width:311px;height:42px;background:var(--white);border-radius:3px;box-shadow:0 2px 8px rgba(0,0,0,.14);display:flex;align-items:center;justify-content:space-between;padding-left:13px}
  .search-text{font-family:"Poppins",sans-serif;font-size:10px;color:#555}
  .search-btn{width:38px;height:38px;background:var(--navy);border-radius:3px;display:flex;align-items:center;justify-content:center;margin-right:2px}

  .menu-btn{position:absolute;left:35px;top:338px}

  .panel-title{position:absolute;left:0;right:0;top:380px;text-align:center;font-weight:500;font-size:18px;color:var(--ink)}
  .pin-label{position:absolute;left:0;right:0;top:422px;text-align:center;font-size:14px;color:var(--muted)}
  .pin-slot{position:absolute;top:481px;width:38px;height:1px;background:var(--line)}
  .send-btn{position:absolute;left:115px;top:519px;width:141px;height:38px;border-radius:19px;background:var(--navy);color:var(--white);font-weight:500;font-size:15px;display:flex;align-items:center;justify-content:center}

  .balances-intro{position:absolute;left:0;right:0;top:372px;text-align:center;font-size:14px;color:var(--muted)}
  .balances-value{position:absolute;left:0;right:0;top:407px;text-align:center;font-size:14px;color:var(--muted)}
  .balances-value strong{font-size:16px;font-weight:500;color:var(--navy)}

  .policy{position:absolute;left:0;right:0;top:698px;text-align:center;font-size:8px;color:#444}
  .tabbar{position:absolute;left:0;right:0;bottom:0;height:40px;background:var(--navy);display:flex;align-items:center;justify-content:center}

  .overlay{position:absolute;inset:0;background:var(--shade)}
  .side-menu{position:absolute;left:0;top:345px;width:196px;height:430px;background:var(--navy);list-style:none;padding-top:16px}
  .side-menu li{display:flex;align-items:center;height:39px;padding-left:35px;color:var(--white);font-size:10.5px;font-weight:500;letter-spacing:-.2px}
  .menu-icon{width:24px;height:24px;border-radius:3px;background:var(--white);margin-right:12px;display:flex;align-items:center;justify-content:center}
  .menu-icon i{display:block;width:14px;height:14px;border-radius:50%}

  .list-head{position:absolute;left:47px;right:46px;top:366px;display:flex;justify-content:space-between;align-items:baseline}
  .list-head h2{font-size:16px;font-weight:500;letter-spacing:.3px}
  .sort{font-size:11px;color:var(--muted)}
  .sort b{font-size:13px;color:var(--navy);margin-left:6px;font-weight:500}
  .day{position:absolute;left:47px;font-size:11px;color:var(--muted);text-decoration:underline;font-weight:500}
  .tx{position:absolute;left:47px;right:46px;height:40px}
  .tx-title{font-size:14px;font-weight:500;color:var(--ink)}
  .tx-time{font-size:10px;color:#444;margin-top:7px}
  .tx-amount{position:absolute;right:0;top:10px;font-size:11px;font-weight:500}
  .tx-amount.in{color:var(--teal)}
  .tx-amount.out{color:var(--ink)}
</style>
</head>
<body>

<svg class="defs" aria-hidden="true">
  <defs>
    <linearGradient id="waveFill" x1="0" y1="0" x2="1" y2="1">
      <stop offset="0" stop-color="#1b2652"/>
      <stop offset=".5" stop-color="#1d5d88"/>
      <stop offset="1" stop-color="#22c0d2"/>
    </linearGradient>
    <symbol id="wave" viewBox="0 0 393 310">
      <path d="M0 0H393V305C372 236 330 196 262 180C200 166 150 168 110 150C55 126 18 70 0 0Z" fill="url(#waveFill)"/>
    </symbol>
    <symbol id="magnifier" viewBox="0 0 24 24">
      <circle cx="10.5" cy="10.5" r="7" fill="none" stroke="#fff" stroke-width="1.6"/>
      <path d="M15.6 15.6L21 21" stroke="#fff" stroke-width="1.8" stroke-linecap="round"/>
    </symbol>
    <symbol id="burger" viewBox="0 0 26 18">
      <path d="M1 2H25M1 9H25M1 16H25" stroke="#1c1b4a" stroke-width="2.6" stroke-linecap="round"/>
    </symbol>
    <symbol id="home" viewBox="0 0 20 20">
      <path d="M10 2L1.5 10H4.5V18H8.5V13H11.5V18H15.5V10H18.5Z" fill="#fff"/>
    </symbol>
    <symbol id="chev" viewBox="0 0 10 6">
      <path d="M1 1L5 5L9 1" fill="none" stroke="currentColor" stroke-width="1.2"/>
    </symbol>
    <symbol id="uparrow" viewBox="0 0 8 14">
      <path d="M4 13V1M1 4L4 1L7 4" fill="none" stroke="currentColor" stroke-width="1.2"/>
    </symbol>
  </defs>
</svg>

<!-- Balances: enter pin -->
<section class="screen s1">
  <svg class="header-wave"><use href="#wave"/></svg>
  <div class="brand"><span class="brand-mark"></span><span class="brand-name">PORLENPURSE</span></div>
  <div class="price-bar"><span class="coin">ZORBS<svg width="10" height="6"><use href="#chev"/></svg></span><span class="value">$ 5.98<svg width="8" height="14"><use href="#uparrow"/></svg></span></div>
  <div class="search"><span class="search-text">Search Here</span><span class="search-btn"><svg width="24" height="24"><use href="#magnifier"/></svg></span></div>
  <svg class="menu-btn" width="26" height="18"><use href="#burger"/></svg>
  <h2 class="panel-title">BALANCES</h2>
  <p class="pin-label">Enter Your Pin Here</p>
  <span class="pin-slot" style="left:52px"></span><span class="pin-slot" style="left:121px"></span><span class="pin-slot" style="left:190px"></span><span class="pin-slot" style="left:259px"></span>
  <div class="send-btn">SEND</div>
  <p class="policy">©Vextaro Zero Liability Transaction Policy</p>
  <nav class="tabbar"><svg width="20" height="20"><use href="#home"/></svg></nav>
</section>

<!-- Balances: result -->
<section class="screen s2">
  <svg class="header-wave"><use href="#wave"/></svg>
  <div class="brand"><span class="brand-mark"></span><span class="brand-name">PORLENPURSE</span></div>
  <div class="price-bar"><span class="coin">ZORBS<svg width="10" height="6"><use href="#chev"/></svg></span><span class="value">$ 5.98<svg width="8" height="14"><use href="#uparrow"/></svg></span></div>
  <div class="search"><span class="search-text">Search Here</span><span class="search-btn"><svg width="24" height="24"><use href="#magnifier"/></svg></span></div>
  <svg class="menu-btn" width="26" height="18"><use href="#burger"/></svg>
  <p class="balances-intro">Your balances are:</p>
  <p class="balances-value">ZORBS <strong>1234567890</strong></p>
  <p class="policy">©Vextaro Zero Liability Transaction Policy</p>
  <nav class="tabbar"><svg width="20" height="20"><use href="#home"/></svg></nav>
</section>

<!-- Menu open -->
<section class="screen s3" style="height:767px">
  <svg class="header-wave"><use href="#wave"/></svg>
  <div class="brand"><span class="brand-mark"></span><span class="brand-name">PORLENPURSE</span></div>
  <div class="price-bar"><span class="coin">ZORBS<svg width="10" height="6"><use href="#chev"/></svg></span><span class="value">$ 5.98<svg width="8" height="14"><use href="#uparrow"/></svg></span></div>
  <div class="search"><span class="search-text">Search Here</span><span class="search-btn"><svg width="24" height="24"><use href="#magnifier"/></svg></span></div>
  <h2 class="panel-title">BALANCES</h2>
  <p class="pin-label">Enter Your Pin Here</p>
  <span class="pin-slot" style="left:52px"></span><span class="pin-slot" style="left:121px"></span><span class="pin-slot" style="left:190px"></span><span class="pin-slot" style="left:259px"></span>
  <div class="send-btn">SEND</div>
  <div class="overlay"></div>
  <svg class="menu-btn" width="26" height="18" style="top:313px"><use href="#burger"/></svg>
  <ul class="side-menu">
    <li><span class="menu-icon" role="img" aria-label="Balances app icon"><i style="background:#b5651d"></i></span>Balances</li>
    <li><span class="menu-icon" role="img" aria-label="Transactions app icon"><i style="background:#7ec8e3"></i></span>Transactions</li>
    <li><span class="menu-icon" role="img" aria-label="Send Money app icon"><i style="background:#f2b632"></i></span>Send Money</li>
    <li><span class="menu-icon" role="img" aria-label="Create Account app icon"><i style="background:#f4a340"></i></span>Create Account</li>
    <li><span class="menu-icon" role="img" aria-label="Wallet Address app icon"><i style="background:#e2553f"></i></span>Wallet Address</li>
    <li><span class="menu-icon" role="img" aria-label="Private Message app icon"><i style="background:#e8454f"></i></span>Private Message</li>
    <li><span class="menu-icon" role="img" aria-label="Buy Cryptocurrency app icon"><i style="background:#2f8ee0"></i></span>Buy Cryptocurrency</li>
    <li><span class="menu-icon" role="img" aria-label="NFTs app icon"><i style="background:#8a6a3a"></i></span>NFTs</li>
    <li><span class="menu-icon" role="img" aria-label="Earn app icon"><i style="background:#e7a13b"></i></span>Earn</li>
    <li><span class="menu-icon" role="img" aria-label="Files and vault app icon"><i style="background:#3a6fd8"></i></span>Files/Vault</li>
    <li><span class="menu-icon" role="img" aria-label="Wealth app icon"><i style="background:#3aa6a0"></i></span>Wealth</li>
  </ul>
</section>

<!-- Transactions: enter pin -->
<section class="screen s4">
  <svg class="header-wave"><use href="#wave"/></svg>
  <div class="brand"><span class="brand-mark"></span><span class="brand-name">PORLENPURSE</span></div>
  <div class="price-bar"><span class="coin">ZORBS<svg width="10" height="6"><use href="#chev"/></svg></span><span class="value">$ 5.98<svg width="8" height="14"><use href="#uparrow"/></svg></span></div>
  <div class="search"><span class="search-text">Search Here</span><span class="search-btn"><svg width="24" height="24"><use href="#magnifier"/></svg></span></div>
  <svg class="menu-btn" width="26" height="18"><use href="#burger"/></svg>
  <h2 class="panel-title">TRANSACTIONS</h2>
  <p class="pin-label">Enter Your Pin Here</p>
  <span class="pin-slot" style="left:52px"></span><span class="pin-slot" style="left:121px"></span><span class="pin-slot" style="left:190px"></span><span class="pin-slot" style="left:259px"></span>
  <div class="send-btn">SEND</div>
  <p class="policy">©Vextaro Zero Liability Transaction Policy</p>
  <nav class="tabbar"><svg width="20" height="20"><use href="#home"/></svg></nav>
</section>

<!-- Transactions: list -->
<section class="screen s5 tall">
  <svg class="header-wave"><use href="#wave"/></svg>
  <div class="brand"><span class="brand-mark"></span><span class="brand-name">PORLENPURSE</span></div>
  <div class="price-bar"><span class="coin">ZORBS<svg width="10" height="6"><use href="#chev"/></svg></span><span class="value">$ 5.98<svg width="8" height="14"><use href="#uparrow"/></svg></span></div>
  <div class="search"><span class="search-text">Search Here</span><span class="search-btn"><svg width="24" height="24"><use href="#magnifier"/></svg></span></div>
  <svg class="menu-btn" width="26" height="18" style="top:332px"><use href="#burger"/></svg>
  <div class="list-head"><h2>TRANSACTIONS</h2><span class="sort">Sort By<b>Date</b> <svg width="8" height="5" style="color:#1c1b4a"><use href="#chev"/></svg></span></div>
  <p class="day" style="top:404px">Today</p>
  <div class="tx" style="top:434px"><p class="tx-title">Lorem Ipsum Is Dummy</p><p class="tx-time">Just Now</p><span class="tx-amount in">+ 50.00 $</span></div>
  <div class="tx" style="top:484px"><p class="tx-title">Lorem Ipsum Is Dummy</p><p class="tx-time">10.45 AM</p><span class="tx-amount out">- 30.00 $</span></div>
  <p class="day" style="top:538px">08 March 2023</p>
  <div class="tx" style="top:568px"><p class="tx-title">Lorem Ipsum Is Dummy</p><p class="tx-time">09.10 AM</p><span class="tx-amount in">+ 50.00 $</span></div>
  <div class="tx" style="top:619px"><p class="tx-title">Lorem Ipsum Is Dummy</p><p class="tx-time">10.45 AM</p><span class="tx-amount out">- 30.00 $</span></div>
  <div class="tx" style="top:670px"><p class="tx-title">Lorem Ipsum Is Dummy</p><p class="tx-time">19.45 PM</p><span class="tx-amount in">+30.00 $</span></div>
  <p class="policy" style="top:707px">©Vextaro Zero Liability Transaction Policy</p>
  <nav class="tabbar"><svg width="20" height="20"><use href="#home"/></svg></nav>
</section>

</body>
</html>
```